Banner Ad Designs for tick and flea products

We sell tick and flea products online and want some great banner designs for our online website to promote our tick and flea products.

The ads must be made up in both Flash and HTML5
Ads can be formatted as .JPEG or .GIF files.

Please see the following url for creative requirements
http://help.bannerkite.com/creative-requirements/

Creative licence no limits to your imagination!

Ads must be created in the following sizes:

- Banner – 468×60
- Square – 250×250
- Small Square – 200×200
- Leaderboard – 728×90
- Medium Rectangle – 300×250
- Chatterly – 100×72

please view our website at www.globalpawstore.com.au or .com to get a feel for our website.

The aim is to attract customers who want to save on tick and flea purchases for their pets (dogs and cats)

Target Market(s)

Anyone who owns a dog or cat

Industry/Entity Type

Online

Font styles to use
Sans Serif
Other font styles liked:
• creative licence on font styles

Requirements
Must have
• Must have a strong urge to entice customers to click through.

Images wording and text etc use creative lic
Nice to have
• Strong appeal to dog and cat owners and how they can save on flea and tick essentials.
Keep it simple but effective.
Be fun and playful and inviting.
Should not have
• Please do not use words like cheap - cheapest

Strobing & Flashing - Strobing, flashing backgrounds, or otherwise distracting ads are not allowed. Do not attempt to overtly distract the user from page content.

```html
<!DOCTYPE html>
<html lang="en">
<head>
<meta charset="utf-8">
<title>Tick and Flea Banner Set – Chatterly 100×72</title>
<link rel="stylesheet" href="https://fonts.googleapis.com/css2?family=Cabin:wght@400;600;700&family=Open+Sans:wght@400&display=swap">
<style>
  :root {
    --page: #ffffff;
    --band: #666666;
    --band-text: #ffffff;
    --leaf: #7dab2f;
    --leaf-dark: #5f8f1c;
    --ink: #ffffff;
    --panel: #ffffff;
    --brand: #1c2f5a;
    --dot: #e0412f;
    --btn-top: #5fe05a;
    --btn-bottom: #169a24;
    --btn-edge: #0f6e1a;
    --btn-text: #0e3d12;
    --photo-a: #f4f8ee;
    --photo-b: #8fbf4a;
    --photo-c: #3c6a2a;
  }
  * { box-sizing: border-box; margin: 0; padding: 0; }
  html, body { width: 1200px; height: 900px; overflow: hidden; background: var(--page); }
  .sheet { position: relative; width: 1200px; height: 900px; font-family: "Cabin", sans-serif; }

  .size-band {
    position: absolute; left: 0; top: 95px; width: 1200px; height: 253px;
    background: var(--band); color: var(--band-text);
    font-family: "Open Sans", sans-serif; text-align: center;
  }
  .size-band__title { position: absolute; left: 0; right: 0; top: 26px; font-size: 30px; font-weight: 400; }
  .size-band__caption { position: absolute; left: 0; right: 0; top: 205px; font-size: 30px; font-weight: 400; }

  .ad { position: absolute; width: 12.5em; height: 9em; overflow: hidden; background: var(--leaf); color: var(--ink); }
  .ad--small { font-size: 12px; top: 174px; }
  .ad--large { font-size: 20.5px; top: 412px; }

  .ad-offer { display: flex; align-items: center; justify-content: center; text-align: center; }
  .ad-offer__text { font-size: 1.6em; line-height: 1.3; font-weight: 400; }

  .ad-photo__image { position: absolute; inset: 0;
    background: radial-gradient(ellipse at 70% 40%, var(--photo-b) 0%, transparent 60%),
                linear-gradient(160deg, var(--photo-a) 0%, var(--photo-b) 55%, var(--photo-c) 100%); }
  .ad-photo__line { position: absolute; font-size: 1.4em; line-height: 1.1; padding: 0 .15em;
    background: rgba(95, 143, 28, .55); white-space: nowrap; }
  .ad-photo__line--first { left: .35em; top: 3.83em; }
  .ad-photo__line--second { right: .1em; top: 4.98em; }

  .ad-save__headline { position: absolute; left: 0; right: 0; top: .55em; text-align: center; font-size: 1.46em; }
  .ad-save__panel { position: absolute; left: .51em; top: 3.29em; width: 11.48em; height: 5.12em;
    background: linear-gradient(to bottom, rgba(255,255,255,.55) 0%, var(--panel) 22%, var(--panel) 100%);
    display: flex; align-items: center; justify-content: center; }

  .ad-order__panel { position: absolute; left: .45em; top: .45em; right: .45em; bottom: .45em;
    background: linear-gradient(to bottom, var(--panel) 0%, var(--panel) 55%, #e6f0da 100%); }
  .ad-order__brand { position: absolute; left: 0; right: 0; top: 1.1em; display: flex; justify-content: center; }
  .ad-order__button { position: absolute; left: 1.1em; top: 5.05em; width: 9.65em; height: 2.56em;
    border-radius: .25em; border: .07em solid var(--btn-edge);
    background: linear-gradient(to bottom, var(--btn-top) 0%, #2fc23a 50%, var(--btn-bottom) 100%);
    display: flex; align-items: center; justify-content: center;
    color: var(--btn-text); font-size: 1em; font-weight: 700; letter-spacing: .02em; }
  .ad-order__button span { font-size: 1.3em; }

  .brand-name { display: flex; align-items: center; gap: .35em; color: var(--brand); font-weight: 600; font-size: 1.05em; white-space: nowrap; }
  .brand-name__dot { width: .9em; height: .9em; border-radius: 50%; background: var(--dot); }
</style>
</head>
<body>
<div class="sheet">
  <section class="size-band">
    <h2 class="size-band__title">Actual Size</h2>
    <p class="size-band__caption">Chatterly – 100×72</p>
  </section>

  <div class="ad ad--small ad-offer" style="left:279px">
    <p class="ad-offer__text">Save on<br>genuine brand<br>tick and flea<br>products</p>
  </div>
  <div class="ad ad--small ad-photo" style="left:447px">
    <div class="ad-photo__image" role="img" aria-label="Photo of a small dog and a tabby cat on a green background"></div>
    <p class="ad-photo__line ad-photo__line--first">Protect</p>
    <p class="ad-photo__line ad-photo__line--second">Your Pets!</p>
  </div>
  <div class="ad ad--small ad-save" style="left:616px">
    <p class="ad-save__headline">Save with us</p>
    <div class="ad-save__panel"><span class="brand-name"><span class="brand-name__dot"></span>Global Paw Store</span></div>
  </div>
  <div class="ad ad--small ad-order" style="left:784px">
    <div class="ad-order__panel">
      <div class="ad-order__brand"><span class="brand-name"><span class="brand-name__dot"></span>Global Paw Store</span></div>
      <div class="ad-order__button"><span>ORDER NOW</span></div>
    </div>
  </div>

  <div class="ad ad--large ad-offer" style="left:46px">
    <p class="ad-offer__text">Save on<br>genuine brand<br>tick and flea<br>products</p>
  </div>
  <div class="ad ad--large ad-photo" style="left:333px">
    <div class="ad-photo__image" role="img" aria-label="Photo of a small dog and a tabby cat on a green background"></div>
    <p class="ad-photo__line ad-photo__line--first">Protect</p>
    <p class="ad-photo__line ad-photo__line--second">Your Pets!</p>
  </div>
  <div class="ad ad--large ad-save" style="left:624px">
    <p class="ad-save__headline">Save with us</p>
    <div class="ad-save__panel"><span class="brand-name"><span class="brand-name__dot"></span>Global Paw Store</span></div>
  </div>
  <div class="ad ad--large ad-order" style="left:910px">
    <div class="ad-order__panel">
      <div class="ad-order__brand"><span class="brand-name"><span class="brand-name__dot"></span>Global Paw Store</span></div>
      <div class="ad-order__button"><span>ORDER NOW</span></div>
    </div>
  </div>
</div>
</body>
</html>
```